Vellisant - Quality health delivered at your door

Vellisant offers home and Community Based Services for adults who wish to continue live independently in their communities. We increase accessibility to health care, reduce health care delivery gap, reduce mortality and morbidity, reduce health while promoting healthy living in the comfort of our patients communities or homes.

We provide on site services and deliver high quality healthcare at your door. Our experienced physicians coordinate care with our certified nurse practitioners and provide chronic care management, physical therapy, rehabilitation and medications management.

Target Market(s)

Older population living in independent living facilities

Industry/Entity Type

Health Care

Contact Information for Business Card

Vellisant

Number of Pages Required

4 page

Font styles to use
Sans Serif

Colors

Designer to choose colors to be used in the design.

```html
<!DOCTYPE html>
<html lang="en">
<head>
<meta charset="utf-8">
<title>Vellisant – Quality health delivered at your door</title>
<link href="https://fonts.googleapis.com/css2?family=Montserrat:wght@400;500;600;700&family=Arimo:wght@400;700&display=swap" rel="stylesheet">
<style>
:root{
  --orange:#f7a11a;
  --olive:#6f8a2a;
  --olive-dark:#5b7420;
  --forest:#22330d;
  --ink:#2b2b2b;
  --grey-text:#555;
  --light:#f2f2f2;
  --white:#fff;
}
*{box-sizing:border-box;margin:0;padding:0}
html,body{width:1200px;height:2711px;overflow:hidden;background:var(--white)}
body{position:relative;font-family:"Arimo",Arial,sans-serif;color:var(--ink)}
.abs{position:absolute}
.heading{font-family:"Montserrat",Arial,sans-serif}

/* header */
.header{left:0;top:0;width:1200px;height:146px}
.brand{left:76px;top:12px;width:180px;text-align:center}
.brand-mark{width:92px;height:92px;border-radius:50%;background:var(--orange);border:5px solid var(--forest);margin:0 auto}
.brand-name{font-family:"Montserrat",Arial,sans-serif;font-weight:500;font-size:24px;color:var(--forest);margin-top:6px;letter-spacing:.5px}
.call{right:78px;top:20px;font-family:"Montserrat",Arial,sans-serif;font-size:20px;color:var(--olive);font-weight:600}
.call strong{font-family:"Arimo",Arial,sans-serif;font-size:29px;color:var(--forest);margin-left:6px}
.btn{display:flex;align-items:center;justify-content:center;font-family:"Montserrat",Arial,sans-serif;font-weight:700;color:var(--white);border-radius:3px}
.btn-join-community{left:829px;top:67px;width:293px;height:49px;background:var(--olive);font-size:19px}

/* nav */
.nav{left:0;top:146px;width:1200px;height:51px;background:var(--forest);display:flex;align-items:center}
.nav-home{width:50px;height:51px;margin-left:78px;background:var(--orange);display:flex;align-items:center;justify-content:center}
.nav a{color:var(--white);text-decoration:none;font-family:"Arimo",Arial,sans-serif;font-size:14.5px;margin-left:15px;white-space:nowrap}
.nav a.first{margin-left:14px}

/* hero */
.hero{left:0;top:197px;width:1200px;height:481px;overflow:hidden}
.hero-photo{left:0;top:0;width:1200px;height:481px;background:linear-gradient(90deg,#d9d2c4 0%,#efe9df 40%,#c9c0b3 100%)}
.hero-title{left:78px;top:132px;font-size:38px;font-weight:500;line-height:57px;color:var(--forest)}
.btn-hero{left:78px;top:269px;width:227px;height:65px;background:var(--olive);font-size:22px;font-weight:600;border-radius:2px}

/* stay home */
.stay{left:0;top:678px;width:1200px;height:415px;background:var(--light)}
.stay h2{position:absolute;left:80px;top:50px;font-family:"Montserrat",Arial,sans-serif;font-weight:400;font-size:40px;color:var(--forest)}
.stay p{position:absolute;left:80px;width:620px;font-size:16.5px;line-height:25px;color:var(--grey-text)}
.stay .p1{top:110px}
.stay .p2{top:186px}
.btn-read{left:78px;top:312px;width:166px;height:53px;background:var(--orange);font-size:19px}
.stay-art{left:810px;top:30px;width:300px;height:300px;border-radius:50%;border:14px solid var(--forest);background:var(--orange)}

/* services */
.services-title{left:0;top:1140px;width:1200px;text-align:center;font-family:"Montserrat",Arial,sans-serif;font-weight:400;font-size:40px;color:var(--forest)}
.service{width:250px;text-align:center}
.service-icon{width:80px;height:80px;margin:0 auto;border-radius:14px;background:var(--olive)}
.service h3{font-family:"Montserrat",Arial,sans-serif;font-weight:500;font-size:19px;line-height:23px;color:var(--forest);margin-top:28px;height:46px;display:flex;align-items:flex-start;justify-content:center}
.service.single h3{height:23px}
.service p{width:240px;margin:6px auto 0;font-size:14px;line-height:22px;color:var(--grey-text)}
.btn-view{left:528px;top:1970px;width:144px;height:52px;background:var(--orange);font-size:19px}

/* testimonial */
.testimonial{left:0;top:2074px;width:1200px;height:261px;background:linear-gradient(90deg,#3f5a1c 0%,#4b6425 50%,#3c521b 100%)}
.quote-badge{left:568px;top:44px;width:64px;height:64px;border-radius:50%;border:3px solid var(--white);display:flex;align-items:center;justify-content:center;color:var(--white);font-family:Georgia,serif;font-size:40px;line-height:1;padding-top:14px}
.quote-text{left:200px;top:122px;width:800px;text-align:center;color:var(--white);font-size:15.5px;line-height:24px}
.quote-name{left:0;top:182px;width:1200px;text-align:center;color:var(--white);font-size:17px;letter-spacing:.5px}
.quote-name em{font-size:15px;letter-spacing:0}

/* footer info */
.footer-info{left:0;top:2335px;width:1200px;height:312px}
.col-title{font-family:"Montserrat",Arial,sans-serif;font-size:25px;color:var(--forest);font-weight:400}
.col-title span{color:var(--orange)}
.col-rule{width:46px;height:3px;background:var(--orange);margin-top:14px}
.about{left:80px;top:42px;width:320px}
.about p{font-size:13.5px;line-height:22px;color:var(--grey-text);margin-top:22px}
.contact{left:435px;top:42px;width:340px}
.contact-row{display:flex;align-items:center;margin-top:18px;font-size:14.5px;color:var(--grey-text);line-height:23px}
.contact-row:first-of-type{margin-top:22px}
.contact-icon{width:44px;height:44px;border-radius:50%;background:var(--olive);border:3px solid var(--forest);flex:none;margin-right:14px;display:flex;align-items:center;justify-content:center}
.foot-brand{left:870px;top:70px;width:180px;text-align:center}
.foot-brand .brand-mark{width:76px;height:76px}
.socials{left:868px;top:200px;display:flex;gap:10px}
.social{width:40px;height:40px;border-radius:50%}

/* bottom bar */
.bottom{left:0;top:2647px;width:1200px;height:64px;background:var(--orange);display:flex;align-items:center;justify-content:space-between;padding:0 78px;color:var(--white);font-size:14.5px}
.bottom strong{color:var(--forest)}
.bottom nav a{color:var(--white);text-decoration:none;margin-left:12px}
</style>
</head>
<body>

<header class="abs header">
  <div class="abs brand">
    <div class="brand-mark"></div>
    <div class="brand-name">VELLISANT</div>
  </div>
  <div class="abs call">CALL US: <strong>123-456-7890</strong></div>
  <a class="abs btn btn-join-community">CLICK TO JOIN COMMUNITY</a>
</header>

<nav class="abs nav">
  <div class="nav-home">
    <svg width="22" height="20" viewBox="0 0 22 20"><path d="M11 1 1 10h3v9h5v-6h4v6h5v-9h3z" fill="#22330d"/></svg>
  </div>
  <a class="first">Assisted Living</a>
  <a>Skilled Nursing</a>
  <a>Independent Living</a>
  <a>Home &amp; Community Based Living</a>
  <a>Respite Care</a>
  <a>Rehabilitation</a>
  <a>Mindara Learning</a>
</nav>

<section class="abs hero">
  <div class="abs hero-photo" role="img" aria-label="Photo of a caregiver kneeling beside a smiling senior woman in a wheelchair"></div>
  <svg class="abs" style="left:0;top:0" width="1200" height="481" viewBox="0 0 1200 481">
    <path d="M0 0H510Q720 240 520 481H0Z" fill="#22330d"/>
    <path d="M0 0H482Q688 240 492 481H0Z" fill="#f7a11a"/>
  </svg>
  <h1 class="abs heading hero-title">Live Independently in<br>Your Communities</h1>
  <a class="abs btn btn-hero">JOIN US NOW</a>
</section>

<section class="abs stay">
  <h2>STAY HOME</h2>
  <p class="p1">Vellisant offers home and Community Based Services for adults who wish to continue to live independently in the comfort of their communities.</p>
  <p class="p2">We provide on site services and deliver high quality healthcare at your door.&nbsp; Our experienced physicians coordinate care with our certified nurse practitioners and provide chronic care management, physical therapy, rehabilitation and medications management.</p>
  <a class="abs btn btn-read">READ MORE</a>
  <div class="abs stay-art" role="img" aria-label="Round illustration of an elderly couple walking together"></div>
</section>

<h2 class="abs services-title">SERVICES</h2>

<div class="abs service" style="left:77px;top:1234px"><div class="service-icon" role="img" aria-label="Medical kit icon"></div><h3>Comprehensive primary<br>Care Services</h3><p>Lorem Ipsum is simply dummy text of the printing and typesetting industry.</p></div>
<div class="abs service" style="left:343px;top:1234px"><div class="service-icon" role="img" aria-label="Specialist care icon"></div><h3>Coordination of Specialty<br>Care</h3><p>Lorem Ipsum is simply dummy text of the printing and typesetting industry.</p></div>
<div class="abs service" style="left:607px;top:1234px"><div class="service-icon" role="img" aria-label="Patient on exam table icon"></div><h3>Chronic<br>Disease Management</h3><p>Lorem Ipsum is simply dummy text of the printing and typesetting industry.</p></div>
<div class="abs service" style="left:872px;top:1234px"><div class="service-icon" role="img" aria-label="Wheelchair assistance icon"></div><h3>Transitional Care</h3><p>Lorem Ipsum is simply dummy text of the printing and typesetting industry.</p></div>

<div class="abs service" style="left:77px;top:1493px"><div class="service-icon" role="img" aria-label="Nurse icon"></div><h3>Skilled Nursing</h3><p>Lorem Ipsum is simply dummy text of the printing and typesetting industry.</p></div>
<div class="abs service" style="left:343px;top:1493px"><div class="service-icon" role="img" aria-label="Social services icon"></div><h3>Social Services<br>Assessment</h3><p>Lorem Ipsum is simply dummy text of the printing and typesetting industry.</p></div>
<div class="abs service" style="left:607px;top:1493px"><div class="service-icon" role="img" aria-label="Home with heart icon"></div><h3>Home Health<br>Assistance</h3><p>Lorem Ipsum is simply dummy text of the printing and typesetting industry.</p></div>
<div class="abs service" style="left:872px;top:1493px"><div class="service-icon" role="img" aria-label="Physical therapy icon"></div><h3>Physical Therapy</h3><p>Lorem Ipsum is simply dummy text of the printing and typesetting industry.</p></div>

<div class="abs service single" style="left:209px;top:1749px"><div class="service-icon" role="img" aria-label="Mental health icon"></div><h3>Mental Health</h3><p>Lorem Ipsum is simply dummy text of the printing and typesetting industry.</p></div>
<div class="abs service single" style="left:475px;top:1749px"><div class="service-icon" role="img" aria-label="Dental chair icon"></div><h3>Dental Health</h3><p>Lorem Ipsum is simply dummy text of the printing and typesetting industry.</p></div>
<div class="abs service single" style="left:739px;top:1749px"><div class="service-icon" role="img" aria-label="Transport van icon"></div><h3>Transportation</h3><p>Lorem Ipsum is simply dummy text of the printing and typesetting industry.</p></div>

<a class="abs btn btn-view">VIEW ALL</a>

<section class="abs testimonial" role="img" aria-label="Soft green-tinted photo of a caregiver with a senior">
  <div class="abs quote-badge">&ldquo;</div>
  <p class="abs quote-text">"Lorem Ipsum is simply dummy text of the printing and typesetting industry. Lorem Ipsum has been the industry's standard dummy text ever since the 1500s, when an unknown printer took a galley."</p>
  <p class="abs quote-name">MARLA JENKINS, <em>Area Name</em></p>
</section>

<section class="abs footer-info">
  <div class="abs about">
    <h4 class="col-title"><span>ABOUT</span> VELLISANT</h4>
    <div class="col-rule"></div>
    <p>Lorem Ipsum is simply dummy text of the printing and typesetting industry. Lorem Ipsum has been the industry's standard dummy text ever since the 1500s, when an unknown printer took a galley of type and scrambled it to make a type specimen book.</p>
  </div>
  <div class="abs contact">
    <h4 class="col-title"><span>CONTACT</span> VELLISANT</h4>
    <div class="col-rule"></div>
    <div class="contact-row"><div class="contact-icon"><svg width="14" height="20" viewBox="0 0 14 20"><path d="M7 0a7 7 0 0 0-7 7c0 5 7 13 7 13s7-8 7-13a7 7 0 0 0-7-7zm0 10a3 3 0 1 1 0-6 3 3 0 0 1 0 6z" fill="#fff"/></svg></div><span>123 Building Name, Street Name, City,<br>Country - Zipcode</span></div>
    <div class="contact-row"><div class="contact-icon"><svg width="18" height="18" viewBox="0 0 18 18"><path d="M4 1 1 3c0 8 6 14 14 14l2-3-4-3-2 2c-2-1-4-3-5-5l2-2z" fill="#fff"/></svg></div><span>123-456-7890</span></div>
    <div class="contact-row"><div class="contact-icon"><svg width="20" height="14" viewBox="0 0 20 14"><rect x="1" y="1" width="18" height="12" fill="none" stroke="#fff" stroke-width="2"/><path d="M1 1l9 7 9-7" fill="none" stroke="#fff" stroke-width="2"/></svg></div><span><em>info@vellisant.com</em></span></div>
  </div>
  <div class="abs brand foot-brand">
    <div class="brand-mark"></div>
    <div class="brand-name" style="font-size:21px">VELLISANT</div>
  </div>
  <div class="abs socials">
    <div class="social" style="background:#3b5998" role="img" aria-label="Social link"></div>
    <div class="social" style="background:#1da1f2" role="img" aria-label="Social link"></div>
    <div class="social" style="background:#dd4b39" role="img" aria-label="Social link"></div>
    <div class="social" style="background:#0077b5" role="img" aria-label="Social link"></div>
  </div>
</section>

<footer class="abs bottom">
  <span>© <strong>VELLISANT</strong> - 2017. All Rights Reserved.</span>
  <nav><a>HOME</a><a>ABOUT</a><a>PRIVACY POLICY</a><a>TERMS &amp; CONDITIONS</a><a>CONTACT</a></nav>
</footer>

</body>
</html>
```